Harbor Wonder Hour - A magic website for a monthly modern magic show

Looking to build a website to promote my new monthly magic show

Sites like this. https://velvetloftshow.example/ https://sevencuriouscardsnight.example/

Target Market(s)

18-65 year old men and women who enjoy live entertainment especially magic

Industry/Entity Type

Entertainment

Coding

Coded - Design and coding required

Number of Pages Required

3 page

Colors

Designer to choose colors to be used in the design.

Requirements
Must have
• Wanting a wordpress site.
• Contact form, media section for photos and videos to be posted.
• A “reviews/testimonials” section.

```html
<!DOCTYPE html>
<html lang="en">
<head>
<meta charset="utf-8">
<title>Harbor Wonder Hour</title>
<link rel="stylesheet" href="https://fonts.googleapis.com/css2?family=Poppins:wght@300;400;500;600;700&display=swap">
<style>
:root{
  --bg:#0c0c0d;
  --bg-footer:#121212;
  --bg-bar:#1f1f1f;
  --red:#ff3a17;
  --red-soft:#ffd9cf;
  --white:#ffffff;
  --muted:#a9a9a9;
  --ink:#1a1a1a;
  --line:#4a4a4a;
}
*{margin:0;padding:0;box-sizing:border-box}
html,body{width:1200px;height:3103px;overflow:hidden;background:var(--bg)}
body{font-family:"Poppins",sans-serif;color:var(--white);position:relative}
.abs{position:absolute}
.hero{left:0;top:0;width:1200px;height:599px;background:radial-gradient(ellipse at 32% 55%,#3d6a86 0%,#1b2a3a 28%,#121a24 55%,#0b0f16 100%)}
.hero-photo{left:0;top:0;width:1200px;height:599px;background:radial-gradient(circle at 38% 58%,rgba(150,200,230,.55) 0,rgba(80,130,170,.25) 14%,transparent 30%),radial-gradient(ellipse at 62% 25%,rgba(90,70,60,.5) 0,transparent 30%)}
.brand-name{left:94px;top:42px;font-size:17px;font-weight:500;white-space:nowrap}
.nav{top:44px;font-size:16px;font-weight:400}
.hero-word{left:985px;top:157px;transform-origin:0 0;transform:rotate(90deg) translateY(-115px);font-size:132px;font-weight:700;line-height:115px;letter-spacing:-2px;white-space:nowrap}
.hero-tag{left:1000px;top:160px;transform-origin:0 0;transform:rotate(90deg);font-size:15px;font-weight:300;white-space:nowrap}
.social-hero{top:536px;width:40px;height:40px;border:1.5px solid var(--white);border-radius:50%}
.learn{left:0;width:1200px;top:549px;text-align:center;font-size:12px}
.learn-line{top:558px;height:1px;width:62px;background:var(--red)}
.section-title{font-weight:600;display:inline-block;position:absolute;line-height:1.1;white-space:nowrap}
.section-title::after{content:"";position:absolute;left:0;right:0;bottom:-3px;height:1.5px;background:linear-gradient(90deg,var(--red),var(--red) 30%,transparent 30%,transparent 70%,var(--red) 70%)}
.center{transform:translateX(-50%)}
.body-text{font-size:12px;line-height:18px;color:var(--muted);font-weight:300}
.btn{display:flex;align-items:center;justify-content:center;border-radius:24px;background:linear-gradient(90deg,var(--red) 0%,#ff6a3c 45%,var(--red-soft) 85%,var(--white) 100%);color:var(--ink);font-weight:600;font-size:14px}
.about-art{left:660px;top:820px;width:420px;height:450px;border-radius:50%;background:radial-gradient(circle at 50% 55%,#c9a640 0,#6b5a2c 14%,#3a3a30 32%,#1a1a1a 55%,transparent 72%)}
.event-img{top:1387px;width:245px;height:179px}
.event-title{top:1585px;font-size:18px;font-weight:600}
.event-text{top:1614px;width:240px;font-size:11px;line-height:18px;color:var(--muted);font-weight:300}
.event-link{top:1659px;font-size:14px;font-weight:600;color:var(--red)}
.video-frame{left:116px;top:1768px;width:484px;height:439px;border:1.5px solid var(--red)}
.video-img{left:94px;top:1745px;width:490px;height:445px;background:radial-gradient(ellipse at 50% 45%,#5c5550 0,#2f2b29 35%,#161515 75%)}
.video-text{font-size:11.5px}
.card{top:2369px;width:479px;height:178px;background:var(--white);color:var(--ink)}
.avatar{top:2351px;width:64px;height:64px;border-radius:50%;border:3px solid var(--red);background:radial-gradient(circle at 50% 40%,#c9a68a,#6c5646)}
.ribbon{top:2370px;width:166px;height:31px;background:linear-gradient(90deg,#ffe3dc,#ffd0c4);border-radius:0 0 40px 0}
.stars{top:2374px;color:#ff1e1e;font-size:22px;letter-spacing:3px}
.reviewer{top:2407px;font-size:12px;font-weight:500}
.quote-text{top:2440px;width:400px;font-size:11px;line-height:18px;color:#555;font-weight:300}
.quote-mark{font-size:44px;font-weight:700;color:#444;line-height:1}
.footer{left:0;top:2614px;width:1200px;height:446px;background:var(--bg-footer)}
.footer-title{font-size:18px;font-weight:600}
.field{left:94px;width:467px;border:1px solid var(--line);font-size:12px;color:var(--muted);padding:12px 24px}
.info{left:643px;font-size:12px;color:var(--muted)}
.info-icon{left:614px;width:18px;height:18px}
.social-foot{top:2919px;width:48px;height:48px;border:2px solid var(--white);border-radius:50%}
.bottom-bar{left:0;top:3060px;width:1200px;height:43px;background:var(--bg-bar);display:flex;align-items:center;justify-content:center;font-size:11px}
.bottom-bar strong{font-weight:500;font-size:14px;margin:0 4px}
</style>
</head>
<body>

<header>
  <div class="abs hero" role="img" aria-label="Magician holding a glowing crystal orb in a dark smoky room"></div>
  <div class="abs hero-photo"></div>
  <div class="abs brand-name">Harbor Wonder Hour</div>
  <nav>
    <div class="abs nav" style="left:705px">Home</div>
    <div class="abs nav" style="left:799px">About Us</div>
    <div class="abs nav" style="left:916px">Events</div>
    <div class="abs nav" style="left:1014px">Contact Us</div>
  </nav>
  <div class="abs hero-word">Magic</div>
  <div class="abs hero-tag">Lorem ipsum is simply</div>
  <div class="abs social-hero" style="left:96px" aria-label="Social link"></div>
  <div class="abs social-hero" style="left:146px" aria-label="Social link"></div>
  <div class="abs social-hero" style="left:190px" aria-label="Social link"></div>
  <div class="abs learn-line" style="left:495px"></div>
  <div class="abs learn">Learn More</div>
  <div class="abs learn-line" style="left:642px"></div>
</header>

<main>
  <section class="welcome">
    <h2 class="section-title center" style="left:600px;top:664px;font-size:43px">Wel Come</h2>
    <p class="abs body-text" style="left:189px;top:723px;width:823px;text-align:center">It is a long established fact that a reader will be distracted by the readable content of a page when looking at its layout. The point of using Lorem Ipsum is that it has a more-or-less normal distribution of letters, as opposed to using 'Content here, content here', making it look like readable English. Many desktop publishing packages and web page editors now use Lorem Ipsum as their default model text,</p>
  </section>

  <section class="about">
    <h2 class="section-title" style="left:96px;top:922px;font-size:43px">About Us</h2>
    <p class="abs body-text" style="left:94px;top:988px;width:430px">There are many variations of passages of Lorem Ipsum available, but the majority have suffered alteration in some form, by injected humour, or domised words which don't look even slightly believable. If you are going to use a passage of Lorem Ipsum, you need to be sure there isn't anything barrassing hidden in the middle of text. All the Lorem Ipsum net tend to repeat predefined chunks as necessary,</p>
    <div class="abs btn" style="left:95px;top:1113px;width:147px;height:45px">Read More</div>
    <div class="abs about-art" role="img" aria-label="Hooded figure with a glowing mask conjuring a spiral of golden light"></div>
  </section>

  <section class="events">
    <h2 class="section-title center" style="left:600px;top:1313px;font-size:43px">Upcoming Events</h2>
    <div class="abs event-img" style="left:94px;background:linear-gradient(135deg,#2a2a36,#14141c)" role="img" aria-label="Card magician with playing cards flying around"></div>
    <div class="abs event-img" style="left:348px;background:linear-gradient(135deg,#c8a23c,#1f5fae 45%,#2a7a6a)" role="img" aria-label="Person in a blue hoodie holding a card in front of a colourful wall"></div>
    <div class="abs event-img" style="left:605px;background:linear-gradient(135deg,#3a2626,#1a1818 60%,#4a4444)" role="img" aria-label="Hand holding a playing card in smoke"></div>
    <div class="abs event-img" style="left:861px;background:linear-gradient(180deg,#2f2f30,#5b4c3d 60%,#8a6a44)" role="img" aria-label="Candles and open books with rising mist"></div>

    <h3 class="abs event-title" style="left:94px">Lorem Ipsum</h3>
    <h3 class="abs event-title" style="left:349px">Lorem Ipsum</h3>
    <h3 class="abs event-title" style="left:606px">Lorem Ipsum</h3>
    <h3 class="abs event-title" style="left:862px">Lorem Ipsum</h3>
    <p class="abs event-text" style="left:95px">Lorem Ipsum is simply dummy text of the printing and typesetting industry.</p>
    <p class="abs event-text" style="left:350px">Lorem Ipsum is simply dummy text of the printing and typesetting industry.</p>
    <p class="abs event-text" style="left:607px">Lorem Ipsum is simply dummy text of the printing and typesetting industry.</p>
    <p class="abs event-text" style="left:863px">Lorem Ipsum is simply dummy text of the printing and typesetting industry.</p>
    <div class="abs event-link" style="left:95px">View Details</div>
    <div class="abs event-link" style="left:350px">View Details</div>
    <div class="abs event-link" style="left:607px">View Details</div>
    <div class="abs event-link" style="left:863px">View Details</div>
  </section>

  <section class="video">
    <div class="abs video-frame"></div>
    <div class="abs video-img" role="img" aria-label="White dove spreading its wings above a magician's hand"></div>
    <h2 class="section-title" style="left:639px;top:1857px;font-size:43px">Video</h2>
    <p class="abs body-text video-text" style="left:639px;top:1932px;width:440px">Lorem Ipsum is simply dummy text of the printing and typesetting industry. Lorem Ipsum has been the industry's standard dummy text ever since the 1500s, when an unknown printer took a galley of type and scrambled it to make a type specimen book. It has survived not only five centuries, but also the leap into electronic typesetting, remaining essentially unchanged.</p>
    <div class="abs btn" style="left:641px;top:2051px;width:148px;height:46px">Click Video</div>
  </section>

  <section class="testimonials">
    <h2 class="section-title center" style="left:600px;top:2271px;font-size:43px">Testimonials</h2>

    <div class="abs card" style="left:114px"></div>
    <div class="abs ribbon" style="left:157px"></div>
    <div class="abs avatar" style="left:95px" role="img" aria-label="Reviewer portrait"></div>
    <div class="abs stars" style="left:175px">★★★★★</div>
    <div class="abs reviewer" style="left:178px;color:var(--ink)">Lorem Ipsum</div>
    <div class="abs quote-mark" style="left:124px;top:2430px">“</div>
    <p class="abs quote-text" style="left:157px">It is a long established fact that a reader will be distracted by the readable content of a page when looking at its layout. The point of using Lorem Ipsum is that it has a more-or-less normal distribution of letters, as opposed to using 'Content here, content here', making it</p>
    <div class="abs quote-mark" style="left:538px;top:2500px">”</div>

    <div class="abs card" style="left:629px"></div>
    <div class="abs ribbon" style="left:672px"></div>
    <div class="abs avatar" style="left:610px" role="img" aria-label="Reviewer portrait"></div>
    <div class="abs stars" style="left:690px">★★★★★</div>
    <div class="abs reviewer" style="left:693px;color:var(--ink)">Lorem Ipsum</div>
    <div class="abs quote-mark" style="left:639px;top:2430px">“</div>
    <p class="abs quote-text" style="left:672px">It is a long established fact that a reader will be distracted by the readable content of a page when looking at its layout. The point of using Lorem Ipsum is that it has a more-or-less normal distribution of letters, as opposed to using 'Content here, content here', making it</p>
    <div class="abs quote-mark" style="left:1053px;top:2500px">”</div>
  </section>
</main>

<footer>
  <div class="abs footer"></div>
  <h2 class="section-title footer-title" style="left:94px;top:2662px">Contact Us</h2>
  <div class="abs field" style="top:2711px;height:43px">Name</div>
  <div class="abs field" style="top:2766px;height:43px">Email</div>
  <div class="abs field" style="top:2822px;height:43px">Phone</div>
  <div class="abs field" style="top:2878px;height:74px">Message</div>
  <div class="abs btn" style="left:99px;top:2970px;width:148px;height:46px">Send Now</div>

  <h2 class="section-title footer-title" style="left:607px;top:2662px">Just Say Hello</h2>
  <svg class="abs info-icon" style="top:2721px" viewBox="0 0 24 24" aria-hidden="true"><path fill="#fff" d="M6.6 10.8a15.1 15.1 0 0 0 6.6 6.6l2.2-2.2c.3-.3.7-.4 1-.2 1.1.4 2.3.6 3.6.6.6 0 1 .4 1 1V20c0 .6-.4 1-1 1A17 17 0 0 1 3 4c0-.6.4-1 1-1h3.5c.6 0 1 .4 1 1 0 1.3.2 2.5.6 3.6.1.3 0 .7-.2 1z"/></svg>
  <div class="abs info" style="top:2720px">212-555-0147</div>
  <svg class="abs info-icon" style="top:2755px" viewBox="0 0 24 24" aria-hidden="true"><rect x="2.5" y="5" width="19" height="14" fill="none" stroke="#fff" stroke-width="1.6"/><path d="M2.5 5l9.5 8 9.5-8" fill="none" stroke="#fff" stroke-width="1.6"/></svg>
  <div class="abs info" style="top:2754px">hello@harborwonderhour.example</div>
  <svg class="abs info-icon" style="top:2789px" viewBox="0 0 24 24" aria-hidden="true"><path fill="#fff" d="M12 2a7 7 0 0 0-7 7c0 5.2 7 13 7 13s7-7.8 7-13a7 7 0 0 0-7-7zm0 9.5A2.5 2.5 0 1 1 12 6.5a2.5 2.5 0 0 1 0 5z"/></svg>
  <div class="abs info" style="top:2788px">18 Pier Lane, Port Alder, WA 98001</div>
  <p class="abs body-text" style="left:612px;top:2840px;width:470px">There are many variations of passages of Lorem Ipsum available, but the majority have suffered alteration in some form, by injected humour, or randomised words which don't look even slightly believable.</p>
  <div class="abs social-foot" style="left:612px" aria-label="Social link"></div>
  <div class="abs social-foot" style="left:675px" aria-label="Social link"></div>
  <div class="abs social-foot" style="left:737px" aria-label="Social link"></div>

  <div class="abs bottom-bar">©2019 <strong>Harbor Wonder Hour</strong>, All rights reserved</div>
</footer>

</body>
</html>
```